Growing the Ironclad Young Contender:
A Family Playbook for Nurturing Bold, Grounded, and Resilient Daughters at Games and Beyond.
📘 Book Cover Design Brief – “Growing the Ironclad Young Contender”

Project Title:
Design a bold, inspiring book cover for a best-selling book titled:
Growing the Ironclad Young Contender
Subtitle: A Family Playbook for Nurturing Bold, Grounded, and Resilient Daughters at Games and Beyond

🎯 Audience:

Parents of female athletes ages 14–20 who want their daughters to build confidence, strength, resilience, and long-term success both in sports and in life.

This book should feel encouraging, empowering, and credible — NOT cheesy, childish, or overly academic.

📕 Design Tone & Style:

Powerful and professional — should feel like a best-selling book from a leading performance or parenting expert

Emotionally compelling — conveys hope, resilience, strength, and possibility

Visually modern and clean — avoid anything overly busy, cliché, or childish

Heroic/aspirational tone — think transformation, leadership, strong positioning

💡 Visual Direction / Ideas (Use as Inspiration, Not Limitation):

Strong, confident teenage female athlete imagery — adaptable beyond one specific sport

Symbolic visuals — e.g. athlete standing strong, on a starting line, looking bold into the future, silhouette, or power stance

Bold typography that feels clean and modern (e.g., Proxima Nova, Montserrat, Gotham, Bebas Neue, etc.)

A title that stands out clearly when viewed as a thumbnail on Brindlemart

Color tones: Empowering, modern, and strong: think deep blues, greens, purples, or golds — avoid playful pastels or overly girly themes

Potential imagery: textured backgrounds, motion, bravery, development, strength, growth, sport/action overlays

🔥 What the Cover MUST Communicate:

✅ This is for parents who want strong, confident female athletes
✅ It’s a guidebook for personal development AND sports performance
✅ It’s about creating “IRONCLAD” confidence — physically, mentally and emotionally
✅ The message is: You can help your daughter become her strongest, most confident self

📚 Back-of-Book Summary (for context):

"Growing the Ironclad Young Contender" is a parent's blueprint to building girls who are strong in body, confident in mind, and ready to lead on and off the field. Through simple strategies around strength training, mindset, nutrition, and character development, this book gives parents the tools to help their daughters stay injury-resistant, break through mental barriers, and unlock their full potential — in sports and in life.

✅ Deliverables:

Full cover design (front, back, spine) for paperback
High-resolution files (print-ready)
Source files (PSD, AI, etc.)
3D mockup versions of the book (standing, flat, stack)

Target Market(s)

Industry/Entity Type

Fitness

Font styles to use
Sans Serif

Colors
FFF300
FFF600
FEFA6F
FFFEC7
FFFEE8

Requirements
Must have
• Bold Font
Should not have
• I don't want an image of a female athlete. I want this to be font based.

```html
<!DOCTYPE html>
<html lang="en">
<head>
<meta charset="utf-8">
<title>Growing the Ironclad Young Contender — Cover</title>
<link href="https://fonts.googleapis.com/css2?family=Montserrat:wght@700;800;900&display=swap" rel="stylesheet">
<style>
  :root {
    --page-bg: #f1f1f1;
    --cover-black: #0d0d0d;
    --cover-black-soft: #1a1a1a;
    --gold-deep: #ad9450;
    --gold-light: #ede3a8;
    --gold-text: #b59d55;
    --white: #ffffff;
  }
  * { margin: 0; padding: 0; box-sizing: border-box; }
  html, body {
    width: 1199px;
    height: 1200px;
    overflow: hidden;
    background: var(--page-bg);
    font-family: "Montserrat", sans-serif;
  }
  .book-cover {
    position: absolute;
    left: 246px;
    top: 69px;
    width: 708px;
    height: 1062px;
    background: radial-gradient(ellipse at 50% 40%, var(--cover-black-soft) 0%, var(--cover-black) 70%);
    overflow: hidden;
  }
  .title-art {
    position: absolute;
    left: 0;
    top: 0;
    width: 708px;
    height: 460px;
  }
  .title-art text {
    font-family: "Montserrat", sans-serif;
    font-weight: 800;
  }
  .hero-visual {
    position: absolute;
    left: 214px;
    top: 470px;
    width: 280px;
    height: 300px;
    border-radius: 140px 140px 24px 24px;
    background: linear-gradient(90deg, var(--gold-deep), var(--gold-light) 55%, var(--gold-deep));
    opacity: 0.85;
  }
  .subtitle {
    position: absolute;
    left: 0;
    top: 797px;
    width: 708px;
    text-align: center;
    font-weight: 700;
    font-size: 24px;
    line-height: 26.5px;
    letter-spacing: 0.3px;
    color: var(--white);
    text-transform: uppercase;
  }
  .subtitle .accent { color: var(--gold-text); }
  .publisher-mark {
    position: absolute;
    left: 0;
    top: 896px;
    width: 708px;
    display: flex;
    flex-direction: column;
    align-items: center;
  }
  .publisher-circle {
    width: 76px;
    height: 76px;
    border-radius: 50%;
    border: 3px solid var(--gold-text);
  }
  .publisher-name {
    margin-top: 12px;
    font-weight: 800;
    font-size: 21px;
    letter-spacing: 1px;
    color: var(--white);
  }
</style>
</head>
<body>
  <main class="book-cover">
    <svg class="title-art" viewBox="0 0 708 460" aria-label="Growing the Ironclad Young Contender">
      <defs>
        <linearGradient id="gold-sheen" x1="0" y1="0" x2="1" y2="0">
          <stop offset="0" stop-color="#ad9450"/>
          <stop offset="0.55" stop-color="#ede3a8"/>
          <stop offset="1" stop-color="#ad9450"/>
        </linearGradient>
      </defs>
      <text x="67" y="121" font-size="75" textLength="577" lengthAdjust="spacingAndGlyphs" fill="url(#gold-sheen)">GROWING THE</text>
      <text x="67" y="219" font-size="103" textLength="577" lengthAdjust="spacingAndGlyphs" fill="#ffffff">IRONCLAD</text>
      <text x="67" y="346" font-size="147" textLength="577" lengthAdjust="spacingAndGlyphs" fill="url(#gold-sheen)">YOUNG</text>
      <text x="67" y="431" font-size="87" textLength="577" lengthAdjust="spacingAndGlyphs" fill="url(#gold-sheen)">CONTENDER</text>
    </svg>

    <div class="hero-visual" role="img" aria-label="Gold silhouette of a sprinting female athlete"></div>

    <p class="subtitle">
      A Family Playbook for Nurturing<br>
      <span class="accent">Bold, Grounded, and Resilient</span><br>
      Daughters at Games and Beyond
    </p>

    <div class="publisher-mark">
      <div class="publisher-circle"></div>
      <div class="publisher-name">IRONCLAD</div>
    </div>
  </main>
</body>
</html>
```